Decorative Candle business needs website designed

We are a new decorative candle business, and we need a website designed. We are looking for a modern/elegant feel to the page. We are working on taking pictures of each of our designs, so that we can display all our designs online.

Our target audience is females aged 16-45

We will need online store facilities also, as we plan to see online.

Please feel free to check out our instagram page for an idea of what we do: @glowsbymirandajoy

I have attached our logo below for use.

```html
<!DOCTYPE html>
<html lang="en">
<head>
<meta charset="utf-8">
<title>Candles – Decorative Candle Shop</title>
<link rel="stylesheet" href="https://fonts.googleapis.com/css2?family=Source+Sans+3:wght@400;600;700;800&display=swap">
<style>
  :root {
    --ink: #0b0b0b;
    --white: #ffffff;
    --paper: #f4f4f4;
    --band: #e6e7e9;
    --nav-top: #5a5a5a;
    --nav-bottom: #2a2a2a;
    --accent: #a3242a;
    --amber: #c77a33;
    --glow: #f0b56a;
    --muted: #9a9a9a;
    --input-text: #b6872f;
    --social: #4a6fb0;
  }
  * { box-sizing: border-box; margin: 0; padding: 0; }
  html, body { width: 802px; height: 1200px; overflow: hidden; }
  body {
    position: relative;
    background: var(--white);
    font-family: "Source Sans 3", "Helvetica Neue", Arial, sans-serif;
    color: var(--ink);
  }
  .abs { position: absolute; }

  /* Header */
  .header-backdrop {
    left: 0; top: 0; width: 802px; height: 334px;
    background:
      radial-gradient(ellipse 70px 40px at 40px 205px, rgba(240,160,90,.55), transparent),
      radial-gradient(ellipse 90px 50px at 760px 205px, rgba(240,170,100,.6), transparent),
      radial-gradient(ellipse 60px 35px at 710px 230px, rgba(230,140,70,.45), transparent),
      radial-gradient(ellipse 220px 80px at 120px 230px, rgba(120,60,30,.4), transparent),
      radial-gradient(ellipse 220px 80px at 700px 230px, rgba(120,60,30,.4), transparent),
      var(--ink);
  }
  .brand {
    left: 62px; top: 12px; width: 90px; height: 58px;
    display: flex; align-items: flex-end; justify-content: center;
    color: var(--white); font-size: 17px; font-weight: 400; letter-spacing: 2px;
  }
  .contact { left: 348px; top: 24px; color: var(--white); font-size: 12px; font-weight: 600; line-height: 17px; }
  .contact div { display: flex; align-items: center; gap: 6px; }
  .socials { display: flex; gap: 6px; }
  .socials span { width: 17px; height: 17px; border-radius: 50%; background: var(--social); display: block; }
  .socials span:nth-child(2) { background: #3fa9dc; }
  .socials span:nth-child(3) { background: #c4302b; }
  .socials span:nth-child(4) { background: #f0a030; }
  .header-socials { left: 575px; top: 12px; }
  .search {
    left: 569px; top: 45px; width: 116px; height: 20px;
    background: var(--white); display: flex; align-items: center; justify-content: space-between;
    padding: 0 6px; font-size: 11px; font-weight: 600;
  }

  /* Hero */
  .hero { left: 87px; top: 89px; width: 626px; height: 365px; background: var(--ink); }
  .nav {
    left: 87px; top: 89px; width: 626px; height: 38px;
    background: linear-gradient(var(--nav-top), var(--nav-bottom));
    display: flex;
  }
  .nav a {
    flex: 1; color: var(--white); text-decoration: none; font-weight: 700; font-size: 15px;
    display: flex; align-items: center; justify-content: center;
    border-right: 2px solid #1c1c1c;
  }
  .nav a:last-child { border-right: none; }
  .slide {
    left: 199px; top: 127px; width: 415px; height: 293px;
    background: linear-gradient(180deg, #b09a86 0%, #e7ddd2 30%, #cdb9a6 70%, #6b564a 100%);
  }
  .slide-caption {
    left: 199px; top: 354px; width: 415px; height: 64px;
    background: rgba(40,40,40,.78); color: var(--white); padding: 6px 12px;
  }
  .slide-caption h2 { font-size: 22px; font-weight: 700; line-height: 26px; }
  .slide-caption p { font-size: 12px; font-weight: 700; }
  .dots { left: 360px; top: 431px; display: flex; gap: 11px; }
  .dots span { width: 14px; height: 14px; border-radius: 50%; background: var(--white); }
  .dots span.active { background: var(--accent); }
  .shadow {
    background: radial-gradient(ellipse at center, rgba(0,0,0,.22), transparent 70%);
  }

  /* Features */
  .feature {
    width: 205px; height: 160px; top: 485px;
    background: var(--ink); border-radius: 30px; color: var(--white);
    text-align: center; padding-top: 20px;
  }
  .feature svg { display: block; margin: 0 auto; }
  .feature h3 { font-size: 17px; font-weight: 400; margin-top: 8px; }
  .feature p { font-size: 7.5px; font-weight: 700; line-height: 9px; padding: 4px 24px 0; }

  /* Product strip */
  .strip { left: 0; top: 698px; width: 802px; height: 182px; background: var(--band); }
  .product { top: 722px; width: 102px; }
  .product .thumb { width: 102px; height: 102px; border: 3px solid var(--white); }
  .product h4 { font-size: 15px; font-weight: 600; margin-top: 10px; line-height: 16px; }
  .product span { font-size: 15px; }
  .arrow { top: 765px; }

  /* Welcome */
  .welcome-icon { left: 135px; top: 915px; }
  .welcome { left: 277px; top: 923px; }
  .welcome h1 { font-size: 32px; font-weight: 800; line-height: 38px; }
  .welcome p { font-size: 14.5px; font-weight: 700; line-height: 15px; }

  /* Footer */
  .footer { left: 0; top: 1067px; width: 802px; height: 133px; background: var(--ink); color: var(--white); }
  .newsletter-label { left: 37px; top: 1113px; font-size: 10.5px; font-weight: 600; color: var(--white); }
  .newsletter { left: 34px; top: 1135px; display: flex; }
  .newsletter .field {
    width: 134px; height: 28px; background: var(--white); color: var(--input-text);
    font-size: 11px; font-weight: 700; display: flex; align-items: center; padding-left: 6px;
  }
  .newsletter .submit {
    width: 59px; height: 28px; background: linear-gradient(#3a3a3a, #1a1a1a);
    color: var(--white); font-size: 11px; font-weight: 700;
    display: flex; align-items: center; justify-content: center;
  }
  .footer-socials { left: 605px; top: 1105px; }
  .copyright { left: 0; top: 1162px; width: 924px; text-align: center; font-size: 11px; color: var(--muted); }
</style>
</head>
<body>
  <header>
    <div class="abs header-backdrop" role="img" aria-label="Dark background with softly blurred warm candle lights"></div>
    <div class="abs brand">Candles</div>
    <div class="abs contact">
      <div>
        <svg width="11" height="8" viewBox="0 0 11 8"><rect x=".5" y=".5" width="10" height="7" fill="none" stroke="#fff"/><path d="M.5 .5 5.5 4.5 10.5 .5" fill="none" stroke="#fff"/></svg>
        hello@glowcandleshop.nl
      </div>
      <div>
        <svg width="11" height="11" viewBox="0 0 11 11"><path d="M2 1h2l1 3-1.5 1a6 6 0 0 0 2.5 2.5L7 6l3 1v2a1 1 0 0 1-1 1A8 8 0 0 1 1 2a1 1 0 0 1 1-1z" fill="#fff"/></svg>
        555-014-2290
      </div>
    </div>
    <div class="abs socials header-socials"><span></span><span></span><span></span><span></span></div>
    <div class="abs search">Search
      <svg width="12" height="12" viewBox="0 0 12 12"><circle cx="5" cy="5" r="3.5" fill="none" stroke="#000" stroke-width="1.6"/><path d="M7.5 7.5 11 11" stroke="#000" stroke-width="2"/></svg>
    </div>
  </header>

  <section>
    <div class="abs shadow" style="left:70px;top:440px;width:660px;height:40px;"></div>
    <div class="abs hero"></div>
    <nav class="abs nav">
      <a href="#">Home</a><a href="#">Products</a><a href="#">Store</a><a href="#">Contact</a><a href="#">About</a>
    </nav>
    <div class="abs slide" role="img" aria-label="Photo of three decorated white pillar candles"></div>
    <div class="abs slide-caption">
      <h2>New Candles</h2>
      <p>Neque porro quisquam est qui dolorem ipsum quia dolor sit amet</p>
    </div>
    <div class="abs dots"><span></span><span class="active"></span><span></span><span></span></div>
  </section>

  <section>
    <div class="abs shadow" style="left:55px;top:630px;width:225px;height:40px;"></div>
    <div class="abs shadow" style="left:291px;top:630px;width:225px;height:40px;"></div>
    <div class="abs shadow" style="left:528px;top:630px;width:225px;height:40px;"></div>

    <div class="abs feature" style="left:65px;">
      <svg width="34" height="44" viewBox="0 0 34 44"><path d="M3 2h20l9 9v31H3z" fill="none" stroke="#fff" stroke-width="3"/><path d="M23 2v9h9" fill="none" stroke="#fff" stroke-width="3"/><path d="M9 20h16M9 27h16M9 34h16" stroke="#fff" stroke-width="3"/></svg>
      <h3>Candle Information</h3>
      <p>Hand poured soy wax candles with cotton wicks. Gentle scents for calm and cosy evenings.</p>
    </div>
    <div class="abs feature" style="left:301px;">
      <svg width="44" height="44" viewBox="0 0 44 44" fill="none" stroke="#fff" stroke-width="2.6"><circle cx="22" cy="22" r="19"/><ellipse cx="22" cy="22" rx="8" ry="19"/><path d="M3 22h38M6 12h32M6 32h32M22 3v38"/></svg>
      <h3>What's New</h3>
      <p>Fresh designs arrive every month. Follow our latest prints, colours and seasonal candle collections here.</p>
    </div>
    <div class="abs feature" style="left:538px;">
      <svg width="46" height="44" viewBox="0 0 46 44"><path d="M2 4h7l6 26h24l5-18H12" fill="none" stroke="#fff" stroke-width="3"/><path d="M14 17h28M15 23h25" stroke="#fff" stroke-width="2.4"/><circle cx="18" cy="38" r="3.5" fill="#fff"/><circle cx="36" cy="38" r="3.5" fill="#fff"/></svg>
      <h3>Promotions</h3>
      <p>Save on gift sets and bundles. Free wrapping on every order placed this month only.</p>
    </div>
  </section>

  <section>
    <div class="abs strip"></div>
    <svg class="abs arrow" style="left:50px;" width="24" height="40" viewBox="0 0 24 40"><path d="M20 4 5 20l15 16" fill="none" stroke="#000" stroke-width="5"/></svg>
    <svg class="abs arrow" style="left:730px;" width="24" height="40" viewBox="0 0 24 40"><path d="M4 4l15 16L4 36" fill="none" stroke="#000" stroke-width="5"/></svg>

    <div class="abs product" style="left:99px;">
      <div class="thumb" role="img" aria-label="Photo of a row of decorated candles" style="background:linear-gradient(180deg,#8a6f6a,#e8dcd8 45%,#5a4842);"></div>
      <h4>Item Name</h4><span>€12,90</span>
    </div>
    <div class="abs product" style="left:221px;">
      <div class="thumb" role="img" aria-label="Photo of patterned pillar candles" style="background:linear-gradient(180deg,#6c5a4a,#e2d6c8 45%,#4d3d33);"></div>
      <h4>Item Name</h4><span>€12,90</span>
    </div>
    <div class="abs product" style="left:342px;">
      <div class="thumb" role="img" aria-label="Photo of a group of candles of different heights" style="background:linear-gradient(180deg,#8d8a86,#eeeae6 50%,#6a645e);"></div>
      <h4>Item Name</h4><span>€12,90</span>
    </div>
    <div class="abs product" style="left:463px;">
      <div class="thumb" role="img" aria-label="Photo of candles with printed designs" style="background:linear-gradient(180deg,#5c544c,#ddd4ca 50%,#3f3832);"></div>
      <h4>Item Name</h4><span>€12,90</span>
    </div>
    <div class="abs product" style="left:584px;">
      <div class="thumb" role="img" aria-label="Photo of decorative candles on a table" style="background:linear-gradient(180deg,#a89a8a,#e6ddd2 45%,#5c4c3e);"></div>
      <h4>Item Name</h4><span>€12,90</span>
    </div>
  </section>

  <section>
    <svg class="abs welcome-icon" width="96" height="94" viewBox="0 0 96 94"><rect x="3" y="3" width="90" height="64" rx="8" fill="none" stroke="#000" stroke-width="6"/><rect x="14" y="13" width="68" height="44" fill="none" stroke="#000" stroke-width="3"/><path d="M40 67v14M56 67v14" stroke="#000" stroke-width="6"/><rect x="24" y="82" width="48" height="8" rx="3" fill="#000"/></svg>
    <div class="abs welcome">
      <h1>Welcome to Candles</h1>
      <p>Lorem ipsum dolor sit amet, consectetur adipiscing elit.<br>Neque porro quisquam est qui dolorem ipsum quia dolor sit amet,</p>
    </div>
  </section>

  <footer>
    <div class="abs footer"></div>
    <div class="abs newsletter-label">Suscribe To Our Newsletter</div>
    <div class="abs newsletter"><div class="field">Enter your email</div><div class="submit">Submit</div></div>
    <div class="abs socials footer-socials"><span></span><span></span><span></span><span></span></div>
    <div class="abs copyright">Copyright 2014 Glowcandleshop.nl</div>
  </footer>
</body>
</html>
```